Event flyer for Sunday night Youth Group

Need a 4 x 6 or 5 x 7 flyer for a new youth group starting on April 14. The youth group is for students in middle school and high school so it needs to look fun and cool, but not childish. I prefer it not to include pictures of people unless it's so obscure you can't really see their faces. I've uploaded some pictures of flyers I like. I've also attached a couple versions of our logo to use on the flyer.
Information the flyer needs to include:
Youth Group
Sundays, 6-8pm (beginning April 14)
Location: Marlowe's - 4219 Quarry Fern Ave N, Keizer, 97318
There will be dinner, games, friends, and a message.
Target Market(s)
Youth ages 13-18
Industry/Entity Type
Church
Font styles to use
Colors
Designer to choose colors to be used in the design.
Look and feel

```html
<!DOCTYPE html>
<html lang="en">
<head>
<meta charset="utf-8">
<title>Youth Group – Sunday Nights</title>
<link href="https://fonts.googleapis.com/css2?family=Montserrat:wght@400;500;600;800;900&family=Cabin:wght@600;700&family=Playball&family=Titan+One&display=swap" rel="stylesheet">
<style>
  :root {
    --navy: #12303d;
    --navy-deep: #0b1c24;
    --teal: #2f5664;
    --slate: #4a6e7a;
    --sage: #9aab9c;
    --brown: #5a3720;
    --brown-warm: #8a4a12;
    --rust: #a0591c;
    --maroon: #4a1420;
    --gold: #d9c27a;
    --paper: #f3f3f1;
    --stage: #ebebeb;
    --ink: #1d2a30;
  }
  * { box-sizing: border-box; margin: 0; padding: 0; }
  html, body {
    width: 1200px; height: 2823px; overflow: hidden;
    background: var(--stage);
  }
  .flyer {
    position: absolute; left: 93px; top: 701px;
    width: 1014px; height: 1420px;
    background: var(--paper);
    overflow: hidden;
    box-shadow: 0 20px 50px rgba(0,0,0,.25);
    font-family: "Montserrat", sans-serif;
  }
  .hero-backdrop {
    position: absolute; left: 0; top: 0; width: 100%; height: 820px;
    background: linear-gradient(180deg, var(--navy-deep) 0%, #142a33 45%, #2a251f 75%, #3a2818 100%);
    clip-path: polygon(0 0, 100% 0, 100% 78%, 88% 84%, 70% 90%, 45% 96%, 25% 92%, 8% 86%, 0 83%);
  }
  .brand {
    position: absolute; top: 75px; left: 0; width: 100%;
    display: flex; justify-content: center; align-items: center; gap: 26px;
  }
  .brand-mark { width: 40px; height: 40px; background: var(--slate); }
  .brand-name {
    font-weight: 600; font-size: 54px; color: var(--slate);
    letter-spacing: 1px; line-height: 1;
  }
  .badge {
    position: absolute; left: 507px; top: 552px;
    transform: translate(-50%, -50%);
    width: 590px; height: 590px;
  }
  .title-script {
    position: absolute; left: 0; width: 100%; top: 360px;
    text-align: center; font-family: "Playball", cursive;
    font-size: 190px; line-height: 1; color: var(--brown-warm);
    transform: rotate(-6deg);
  }
  .title-block {
    position: absolute; left: 0; width: 100%; top: 548px;
    text-align: center; font-family: "Titan One", sans-serif;
    font-size: 150px; line-height: 1; color: var(--navy);
    letter-spacing: -2px;
  }
  .pill {
    position: absolute; color: #fff; display: flex; align-items: center; justify-content: center;
  }
  .pill-beginning {
    left: 262px; top: 792px; width: 490px; height: 82px;
    background: var(--teal); border-radius: 22px 22px 0 0;
    font-weight: 500; font-size: 64px; letter-spacing: 1px;
  }
  .pill-day {
    left: 204px; top: 877px; width: 290px; height: 120px;
    background: var(--navy); border-radius: 22px 0 0 22px;
    font-weight: 900; font-size: 104px;
  }
  .pill-day sup { font-size: 44px; margin-left: 4px; align-self: flex-start; margin-top: 10px; }
  .pill-month {
    left: 482px; top: 868px; width: 332px; height: 120px;
    background: var(--brown); border-radius: 22px;
    font-weight: 900; font-size: 80px;
  }
  .schedule {
    position: absolute; top: 1012px; width: 100%; text-align: center;
    font-weight: 900; font-size: 84px; letter-spacing: 1px;
  }
  .schedule .days { color: var(--brown); }
  .schedule .hours { color: var(--navy); }
  .location-label {
    position: absolute; top: 1136px; width: 100%; text-align: center;
    font-weight: 600; font-size: 22px; letter-spacing: 5px; color: var(--ink);
  }
  .location-box {
    position: absolute; left: 100px; top: 1159px; width: 814px; height: 66px;
    border: 2px solid var(--rust); border-top: none;
    display: flex; align-items: center; justify-content: center;
    font-family: "Cabin", sans-serif; font-weight: 700; font-size: 31px; color: var(--navy);
  }
  .location-box::before, .location-box::after {
    content: ""; position: absolute; top: 0; height: 2px; background: var(--rust); width: 305px;
  }
  .location-box::before { left: 0; }
  .location-box::after { right: 0; }
  .location-box .venue { color: var(--brown-warm); margin-right: 8px; }
  .extras-label {
    position: absolute; top: 1262px; width: 100%; text-align: center;
    font-weight: 600; font-size: 21px; letter-spacing: 3px; color: var(--ink);
  }
  .extras {
    position: absolute; top: 1296px; width: 100%;
    display: flex; justify-content: center; list-style: none;
    font-family: "Cabin", sans-serif; font-weight: 700; font-size: 27px;
  }
  .extras li { padding: 8px 26px; border-left: 2px solid var(--ink); }
  .extras li:first-child { border-left: none; }
  .extras .navy { color: var(--navy); }
  .extras .brown { color: var(--brown-warm); }
</style>
</head>
<body>
  <main class="flyer">
    <div class="hero-backdrop" role="img" aria-label="Dim backdrop of raised hands in silhouette fading into a brown brush stroke"></div>

    <header class="brand">
      <span class="brand-mark"></span>
      <span class="brand-name">Waypoint Fellowship</span>
    </header>

    <svg class="badge" viewBox="0 0 590 590" aria-hidden="true">
      <defs>
        <linearGradient id="ringGold" x1="0" y1="0" x2="1" y2="1">
          <stop offset="0" stop-color="#b89a4a"/>
          <stop offset=".5" stop-color="#f3e6a8"/>
          <stop offset="1" stop-color="#a8883a"/>
        </linearGradient>
        <radialGradient id="discFill" cx=".5" cy=".45" r=".55">
          <stop offset="0" stop-color="#ffffff"/>
          <stop offset=".85" stop-color="#f2f0f1"/>
          <stop offset="1" stop-color="#d9d6d8"/>
        </radialGradient>
      </defs>
      <circle cx="295" cy="295" r="288" fill="none" stroke="url(#ringGold)" stroke-width="8"/>
      <circle cx="295" cy="295" r="268" fill="var(--navy-deep)"/>
      <circle cx="295" cy="295" r="254" fill="url(#discFill)"/>
    </svg>

    <h1>
      <span class="title-script">Youth</span>
      <span class="title-block">GROUP</span>
    </h1>

    <div class="pill pill-beginning">BEGINNING</div>
    <div class="pill pill-day">14<sup>TH</sup></div>
    <div class="pill pill-month">APRIL</div>

    <p class="schedule"><span class="days">SUNDAYS,</span> <span class="hours">6-8PM</span></p>

    <p class="location-label">LOCATION:</p>
    <p class="location-box"><span class="venue">Marlowe's -</span> 4219 Quarry Fern Ave N, Keizer, 97318</p>

    <p class="extras-label">THERE WILL BE</p>
    <ul class="extras">
      <li class="navy">DINNER</li>
      <li class="brown">FRIENDS</li>
      <li class="navy">GAMES</li>
      <li class="brown">MESSAGE</li>
    </ul>
  </main>
</body>
</html>
```